Business Card Design

We are a commercial real estate brokerage in San Francisco, leasing office buildings downtown.
I would like a clean, elegant look. Simple but powerful .

Industry/Entity Type

Business

Contact Information for Business Card

Derek Holloway
lic# 07258143
415.555.0172
derek@velt-commercial.example
velt-commercial.example

```html
<!DOCTYPE html>
<html lang="en">
<head>
<meta charset="utf-8">
<title>Velt Commercial — Business Card</title>
<link rel="stylesheet" href="https://fonts.googleapis.com/css2?family=Source+Sans+3:ital,wght@0,400;0,600;1,400&display=swap">
<style>
  :root {
    --backdrop: #8e8f91;
    --card: #e9eaec;
    --slate: #6a7c99;
    --ink: #3b3b3e;
    --ink-soft: #4a4a4e;
    --band-text: #f2f3f6;
  }
  * { box-sizing: border-box; margin: 0; padding: 0; }
  html, body {
    width: 1105px;
    height: 1200px;
    overflow: hidden;
    background: var(--backdrop);
    font-family: "Source Sans 3", "Myriad Pro", sans-serif;
  }
  .card {
    position: absolute;
    left: 180px;
    width: 745px;
    height: 425px;
    background: var(--card);
    overflow: hidden;
  }
  .card--front { top: 119px; }
  .card--back { top: 635px; }

  /* Front */
  .edge-strip {
    position: absolute;
    right: 0; top: 0;
    width: 16px; height: 100%;
    background: var(--slate);
  }
  .brand {
    position: absolute;
    left: 83px; top: 72px;
    display: flex;
    align-items: center;
    height: 88px;
  }
  .brand-square {
    width: 62px; height: 62px;
    background: var(--slate);
  }
  .brand-divider {
    width: 2px; height: 88px;
    background: var(--ink);
    margin: 0 12px 0 22px;
  }
  .brand-name {
    color: var(--ink);
    font-weight: 600;
    line-height: 1;
  }
  .brand-name .primary { display: block; font-size: 56px; letter-spacing: 1px; }
  .brand-name .secondary { display: block; font-size: 25px; letter-spacing: 0.5px; margin-top: 2px; }

  .person {
    position: absolute;
    left: 83px; top: 193px;
  }
  .person-name {
    color: var(--slate);
    font-size: 27px;
    font-weight: 600;
    letter-spacing: 0.5px;
    text-transform: uppercase;
  }
  .person-license {
    color: var(--ink-soft);
    font-size: 19px;
    margin-top: 2px;
  }
  .contact-list {
    position: absolute;
    left: 83px; top: 271px;
    list-style: none;
  }
  .contact-list li {
    display: flex;
    align-items: center;
    height: 29px;
    color: var(--ink-soft);
    font-size: 19.5px;
  }
  .contact-list svg {
    width: 18px; height: 18px;
    margin-right: 10px;
    fill: var(--ink-soft);
  }

  /* Back */
  .back-mark {
    position: absolute;
    left: 0; right: 0; top: 140px;
    text-align: center;
    color: var(--ink);
    font-weight: 600;
    line-height: 1;
  }
  .back-mark .primary { display: block; font-size: 68px; letter-spacing: 2px; }
  .back-mark .secondary { display: block; font-size: 30px; letter-spacing: 1px; margin-top: 6px; }
  .tagline-band {
    position: absolute;
    left: 0; bottom: 0;
    width: 100%; height: 85px;
    background: var(--slate);
    display: flex;
    flex-direction: column;
    align-items: center;
    justify-content: center;
    color: var(--band-text);
    font-style: italic;
    font-size: 19.5px;
    line-height: 1.35;
  }
</style>
</head>
<body>
  <section class="card card--front">
    <div class="edge-strip"></div>
    <div class="brand">
      <div class="brand-square"></div>
      <div class="brand-divider"></div>
      <div class="brand-name">
        <span class="primary">VELT</span>
        <span class="secondary">COMMERCIAL</span>
      </div>
    </div>
    <div class="person">
      <p class="person-name">Derek Holloway</p>
      <p class="person-license">lic# 07258143</p>
    </div>
    <ul class="contact-list">
      <li>
        <svg viewBox="0 0 24 24" aria-hidden="true"><path d="M6.6 10.8a15.1 15.1 0 0 0 6.6 6.6l2.2-2.2c.3-.3.7-.4 1-.2 1.1.4 2.3.6 3.6.6.6 0 1 .4 1 1V20c0 .6-.4 1-1 1A17 17 0 0 1 3 4c0-.6.4-1 1-1h3.5c.6 0 1 .4 1 1 0 1.3.2 2.5.6 3.6.1.3 0 .7-.2 1z"/></svg>
        415.555.0172
      </li>
      <li>
        <svg viewBox="0 0 24 24" aria-hidden="true"><path d="M2 6h20v12H2z M3.5 7.2 12 13l8.5-5.8" fill="none" stroke="currentColor"/><path d="M2 5h20v14H2V5zm2 2v.3l8 5.2 8-5.2V7H4z"/></svg>
        derek@velt-commercial.example
      </li>
      <li>
        <svg viewBox="0 0 24 24" aria-hidden="true"><path d="M12 2a10 10 0 1 0 0 20 10 10 0 0 0 0-20zm-1 17.9A8 8 0 0 1 4.2 10.6L9 15v1a2 2 0 0 0 2 2v1.9zm6.9-2.5A2 2 0 0 0 16 16h-1v-3a1 1 0 0 0-1-1H8v-2h2a1 1 0 0 0 1-1V7h2a2 2 0 0 0 2-2v-.4a8 8 0 0 1 2.9 12.8z"/></svg>
        velt-commercial.example
      </li>
    </ul>
  </section>

  <section class="card card--back">
    <div class="back-mark">
      <span class="primary">VELT</span>
      <span class="secondary">COMMERCIAL</span>
    </div>
    <div class="tagline-band">
      <p>commercial real estate brokerage in San Francisco</p>
      <p>leasing office buildings downtown.</p>
    </div>
  </section>
</body>
</html>
```